Its time for a new website

We are at a point now where we are in desperate need of a new website. It was last updated 2006 but still looks like its 1995. We are looking for something eye catching to our clients but easy to navigate and add/remove photos of jobs/trucks and information. Our key business is the manufacture of fire appliances and resale of parts and equipment.

www.kestrelrigs.com.au

Coding

Coded - Design and coding required

Number of Pages Required

5+ page

Requirements
Must have
• Logo

```html
<!DOCTYPE html>
<html lang="en">
<head>
<meta charset="utf-8">
<title>Kestrel Rigs — Custom Firefighting Equipment</title>
<link href="https://fonts.googleapis.com/css2?family=Oswald:wght@300;400;500;600&family=Open+Sans:wght@400&display=swap" rel="stylesheet">
<style>
:root{
  --bg:#1e1412;
  --bg-header:#1f1513;
  --red:#dd0a0a;
  --blue:#1f7fc9;
  --text:#e8e2e0;
  --muted:#b9b1ae;
  --rule:#34211d;
  --cond:'Oswald', sans-serif;
  --body:'Open Sans', sans-serif;
}
*{box-sizing:border-box;margin:0;padding:0}
html,body{width:845px;height:1200px;overflow:hidden;background:var(--bg);color:var(--text)}
.page{position:relative;width:845px;height:1200px}
.abs{position:absolute}
.cond{font-family:var(--cond);letter-spacing:-0.3px}

/* header */
.site-header{position:absolute;left:0;top:0;width:845px;height:100px;background:var(--bg-header)}
.brand{left:70px;top:34px;display:flex;align-items:center;gap:8px}
.brand-dot{width:22px;height:22px;border-radius:50%;background:var(--red)}
.brand-name{font-family:var(--cond);font-weight:400;font-size:20px;color:var(--blue)}
.call{left:537px;top:26px;font-size:11px;font-weight:400;color:#fff}
.btn{background:var(--red);color:#fff;font-family:var(--cond);font-weight:400;display:flex;align-items:center;justify-content:center}
.btn-new{left:702px;top:18px;width:73px;height:30px;font-size:11px}
.nav{top:67px;font-family:var(--cond);font-weight:300;font-size:11px;color:#fff}
.nav.active{color:var(--blue)}

/* hero */
.hero{left:0;top:100px;width:845px;height:363px;
  background:linear-gradient(135deg,#2a2532 0%,#33272a 50%,#3d2a22 100%)}
.hero-title{left:0;width:845px;top:218px;text-align:center;font-family:var(--cond);font-weight:600;font-size:28px;letter-spacing:-0.6px;color:#fff}
.hero-sub{left:0;width:845px;top:260px;text-align:center;font-family:var(--cond);font-weight:500;font-size:18px;letter-spacing:-0.5px;color:#fff}
.btn-hero{left:365px;top:301px;width:115px;height:30px;font-size:13px}
.arrow{top:248px}

/* features */
.feature{width:210px;text-align:center}
.feature h3{font-family:var(--cond);font-weight:400;font-size:14px;color:var(--blue);margin-top:8px;margin-bottom:10px}
.feature p{font-family:var(--body);font-size:8.6px;line-height:16.3px;color:var(--text)}
.btn-read{width:65px;height:28px;font-size:10.5px;margin:15px auto 0}
.divider{left:0;top:771px;width:845px;height:1px;background:var(--rule)}

/* lower */
.col-title{top:806px;font-family:var(--cond);font-weight:400;font-size:14px;color:var(--blue)}
.pager{top:803px;width:25px;height:25px;border-radius:50%;background:#2c2220}
.work-photo{left:70px;top:850px;width:221px;height:171px;border:3px solid #3a2a26;
  background:linear-gradient(160deg,#8d8884 0%,#7a5e58 100%)}
.news{left:357px;width:228px;font-family:var(--body);font-size:8.6px;line-height:16.3px}
.news-date{font-family:var(--cond);font-weight:300;font-size:11px;color:var(--red);margin-top:4px}
.view-more{left:357px;top:1008px;font-family:var(--cond);font-weight:300;font-size:10px}
.contact{left:627px;top:848px;width:156px;font-family:var(--body);font-size:8.6px;line-height:16.3px}

/* band + footer */
.band{left:0;top:1070px;width:845px;height:42px;background:var(--red);display:flex;align-items:center;justify-content:center;gap:10px}
.band span{font-family:var(--cond);font-weight:500;font-size:12px;letter-spacing:-0.4px;color:#fff}
.band-icon{width:15px;height:15px;border-radius:50%;background:#1e1412}
.social{top:1128px;width:27px;height:27px;border-radius:50%;background:#2c2220}
.copyright{left:0;width:845px;top:1167px;text-align:center;font-family:var(--body);font-size:7.6px;color:var(--muted)}
</style>
</head>
<body>
<div class="page">

  <header class="site-header">
    <div class="abs brand"><span class="brand-dot"></span><span class="brand-name">Kestrel Rigs</span></div>
    <div class="abs call cond">CALL US: 08 9555 0142, 61 8 9555 0142</div>
    <div class="abs btn btn-new">NEW FOR 2015</div>
    <nav>
      <span class="abs nav active" style="left:238px">HOME</span>
      <span class="abs nav" style="left:286px">ABOUT US</span>
      <span class="abs nav" style="left:344px">PUMPERS</span>
      <span class="abs nav" style="left:404px">TANKERS</span>
      <span class="abs nav" style="left:460px">GPA/RESUE</span>
      <span class="abs nav" style="left:523px">LIGHT TANKERS</span>
      <span class="abs nav" style="left:602px">TRAILERS</span>
      <span class="abs nav" style="left:658px">SLIP-ON UNITS</span>
      <span class="abs nav" style="left:732px">CONTACT US</span>
    </nav>
  </header>

  <section>
    <div class="abs hero" role="img" aria-label="Workshop photo of a welder fabricating equipment"></div>
    <svg class="abs arrow" style="left:20px" width="26" height="58" viewBox="0 0 26 58"><polyline points="25,1 1,29 25,57" fill="none" stroke="#fff" stroke-width="1.2"/></svg>
    <svg class="abs arrow" style="left:795px" width="26" height="58" viewBox="0 0 26 58"><polyline points="1,1 25,29 1,57" fill="none" stroke="#fff" stroke-width="1.2"/></svg>
    <h1 class="abs hero-title">KESTREL RIGS ARE WESTERN AUSTRALIA'S</h1>
    <h2 class="abs hero-sub">LEADING MANUFACTURER OF CUSTOM FIREFIGHTING EQUIPMENT</h2>
    <div class="abs btn btn-hero">2015 APPLIANCES</div>
  </section>

  <section>
    <div class="abs feature" style="left:65px;top:501px">
      <svg width="86" height="86" viewBox="0 0 86 86"><path d="M43 2 A41 41 0 0 0 43 84" fill="none" stroke="var(--red)" stroke-width="4"/><path d="M43 2 A41 41 0 0 1 43 84" fill="none" stroke="var(--blue)" stroke-width="4"/><circle cx="43" cy="43" r="34" fill="#2a1e1b"/><circle cx="43" cy="43" r="14" fill="#9c9c9c" role="img" aria-label="Pumper truck icon"/></svg>
      <h3>PUMPERS</h3>
      <p>ur range of pumpers have been specifically designed for use in a broad range of areas such as metropolitan, industrial and mining applicationssuit specific brigade requirements.</p>
      <div class="btn btn-read">READ MORE</div>
    </div>
    <div class="abs feature" style="left:317px;top:501px">
      <svg width="86" height="86" viewBox="0 0 86 86"><path d="M43 2 A41 41 0 0 0 43 84" fill="none" stroke="var(--red)" stroke-width="4"/><path d="M43 2 A41 41 0 0 1 43 84" fill="none" stroke="var(--blue)" stroke-width="4"/><circle cx="43" cy="43" r="34" fill="#2a1e1b"/><circle cx="43" cy="43" r="14" fill="#9c9c9c" role="img" aria-label="Tanker truck icon"/></svg>
      <h3>TANKERS</h3>
      <p>ur range of pumpers have been specifically designed for use in a broad range of areas such as metropolitan, industrial and mining applicationssuit specific brigade requirements.</p>
      <div class="btn btn-read">READ MORE</div>
    </div>
    <div class="abs feature" style="left:565px;top:501px">
      <svg width="86" height="86" viewBox="0 0 86 86"><path d="M43 2 A41 41 0 0 0 43 84" fill="none" stroke="var(--red)" stroke-width="4"/><path d="M43 2 A41 41 0 0 1 43 84" fill="none" stroke="var(--blue)" stroke-width="4"/><circle cx="43" cy="43" r="34" fill="#2a1e1b"/><circle cx="43" cy="43" r="14" fill="#9c9c9c" role="img" aria-label="Trailer truck icon"/></svg>
      <h3>TRAILERS</h3>
      <p>ur range of pumpers have been specifically designed for use in a broad range of areas such as metropolitan, industrial and mining applicationssuit specific brigade requirements.</p>
      <div class="btn btn-read">READ MORE</div>
    </div>
    <div class="abs divider"></div>
  </section>

  <section>
    <h4 class="abs col-title" style="left:69px">OUR WORKS</h4>
    <svg class="abs pager" style="left:239px" viewBox="0 0 25 25"><polyline points="14,8 10,12.5 14,17" fill="none" stroke="#fff" stroke-width="2"/></svg>
    <svg class="abs pager" style="left:266px" viewBox="0 0 25 25"><polyline points="11,8 15,12.5 11,17" fill="none" stroke="#fff" stroke-width="2"/></svg>
    <div class="abs work-photo" role="img" aria-label="Photo of a completed foam tanker truck"></div>

    <h4 class="abs col-title" style="left:358px">FOR ALL YOUR FIRE FIGHTING NEEDS</h4>
    <div class="abs news" style="top:848px">
      <p>A 7200 Litre Foam Tanker comprises of a Multi-baffled and internally lined Stainless Steel tank Based on a Harlan HX6 single-cab. Featured with a Huge Full Width</p>
      <p class="news-date">Last Update 10 April, 2006</p>
    </div>
    <div class="abs news" style="top:940px">
      <p>A 7200 Litre Foam Tanker comprises of a Multi-baffled and internally lined Stainless Steel tank Based.</p>
      <p class="news-date">Last Update 10 April, 2006</p>
    </div>
    <div class="abs view-more">{View More}</div>

    <h4 class="abs col-title" style="left:627px">CONTACT US</h4>
    <div class="abs contact">
      <p>Kestrel Rigs manufacture quality fire truck and tender units in the South West region of Australia</p>
      <p style="margin-top:16px">Lot 14 Banksia Road Wandering 6308<br>Western Australia<br>Phone 08 9555 0142 ------<br>Phone (International) +61 8 9555 0142<br>Fax 08 9555 0187 ------<br>Fax (International) +61 8 9555 0187<br>email Address</p>
    </div>
  </section>

  <div class="abs band"><span>CLICK HERE—EMPLOYMENT OPPORTUNITIES—CLICK HERE</span>
    <svg class="band-icon" viewBox="0 0 15 15"><polyline points="6,4.5 9,7.5 6,10.5" fill="none" stroke="#fff" stroke-width="1.5"/></svg></div>

  <footer>
    <span class="abs social" style="left:326px"></span>
    <span class="abs social" style="left:359px"></span>
    <span class="abs social" style="left:392px"></span>
    <span class="abs social" style="left:425px"></span>
    <span class="abs social" style="left:458px"></span>
    <span class="abs social" style="left:491px"></span>
    <p class="abs copyright">© Copyright 2015 kestrelrigs.com.au &nbsp;All Rights Reserved &nbsp;| &nbsp;Sitemap</p>
  </footer>
</div>
</body>
</html>
```